Valdane Companies Business Card Design

We need a new business card for our Private Equity Real Estate Development firm, “Valdane” and our EB-5 regional center “Thornmere Regional Center” on one card. We prefer a design that is simple, elegant, and represents the luxury products we design and build as well as the financial security and stability our successful history has produced. We are an industry leader in our field and 3rd generation family business that has evolved into an institutional quality investment platform. Considered design size is standard business card dimensions (3.5 x 2 inches with an additional 1/8 inch space for design elements or backgrounds that extend beyond the finished size of your piece.

Target Market(s)

• High net worth individuals
• Highly skilled technical workers and physicians in the US seeking investment-based immigration opportunities
• Sophisticated private equity investors
• Intermediary partners include domestic attorneys and investment brokers, as well as international agent networks
• US real estate developers

Industry/Entity Type

Finance

Contact Information for Business Card

(Providing placeholder info for personal information, please design for longer character spaces, longer names and addresses etc..)
• Logo for Valdane
• Logo for Thornmere Regional Center
• Full name: Marcus Valdane
• Job title: CEO
• Email address: mvaldane@valdanecompanies.com
• Cell phone number: +1.555.314.2287
• Office number +1.555.628.4410
• Office address: Larkfield Court 5, 4817 Vista Orilla, Corvell Bay, CV.
• Website: www.valdanecompanies.com

Font styles to use
Serif
Sans Serif

Colors
ec1f27
ffffff
000000

Requirements
Must have
• • Logo for Valdane
• • Logo for Thornmere Regional Center
• - Use rounded corners
• (See .ai file included for logos)
Nice to have
• • Simple, elegant design
• • Aesthetically compatible with our website design (www.valdanecompanies.com)
• • Color palette including but not limited to white, black, and red (as per logos)
Should not have
• - Not too much red color
• - Do not stack both logos on top of each other

```html
<!DOCTYPE html>
<html lang="en">
<head>
<meta charset="utf-8">
<title>Valdane Capital – Business Card</title>
<link rel="stylesheet" href="https://fonts.googleapis.com/css2?family=Crimson+Pro:wght@400;700&display=swap">
<style>
  :root {
    --bg: #3a3a3c;
    --brand-red: #a51c30;
    --accent-red: #c8203a;
    --card-black: #0e0e0e;
    --card-black-soft: #262626;
    --white: #ffffff;
    --logo-grey: #8a8a8a;
    --text-light: #f2f2f2;
  }
  * { box-sizing: border-box; margin: 0; padding: 0; }
  html, body { width: 1200px; height: 1000px; overflow: hidden; }
  body {
    background: radial-gradient(ellipse at 55% 40%, #5a5a5c 0%, var(--bg) 70%);
    font-family: "Crimson Pro", Georgia, serif;
    position: relative;
  }
  .card {
    position: absolute;
    width: 660px;
    height: 378px;
    border-radius: 26px;
    overflow: hidden;
    box-shadow: 0 18px 40px rgba(0,0,0,.45);
  }

  /* Front */
  .card-front {
    left: 400px; top: 60px;
    background: var(--brand-red);
    display: flex; align-items: center; justify-content: center;
  }
  .front-brand {
    display: flex; align-items: center; gap: 18px;
    color: var(--white);
    font-weight: 700;
    font-size: 54px;
    letter-spacing: 3px;
    text-transform: uppercase;
    white-space: nowrap;
  }
  .front-brand .mark { width: 38px; height: 38px; background: var(--white); }

  /* Back */
  .card-back {
    left: 140px; top: 500px;
    background: radial-gradient(ellipse at 45% 25%, var(--card-black-soft) 0%, var(--card-black) 70%);
  }
  .back-wave { position: absolute; left: 0; bottom: 0; width: 660px; height: 378px; }
  .brand-column {
    position: absolute; left: 24px; top: 96px; width: 264px;
    display: flex; flex-direction: column; align-items: center; gap: 22px;
  }
  .brand-main {
    color: var(--logo-grey);
    font-weight: 700; font-size: 36px; letter-spacing: 1.5px;
    text-transform: uppercase; text-align: center; line-height: 1.05;
  }
  .brand-partner {
    display: flex; align-items: center; gap: 7px;
    color: var(--accent-red);
    font-weight: 700; font-size: 14px; letter-spacing: .3px;
    text-transform: uppercase;
    white-space: nowrap;
  }
  .brand-partner .mark { width: 12px; height: 12px; background: var(--accent-red); flex: none; }
  .divider {
    position: absolute; left: 300px; top: 62px;
    width: 2px; height: 198px; background: var(--accent-red);
  }
  .contact {
    position: absolute; left: 326px; top: 60px;
    color: var(--text-light);
  }
  .contact .name { font-weight: 700; font-size: 24px; letter-spacing: .5px; text-transform: uppercase; white-space: nowrap; }
  .contact .title { font-size: 13px; margin-bottom: 16px; }
  .contact .address { font-size: 16px; line-height: 1.25; margin-bottom: 6px; white-space: nowrap; }
  .contact-list { list-style: none; font-size: 16px; line-height: 1.4; }
  .contact-list li { display: flex; align-items: center; gap: 8px; white-space: nowrap; }
  .contact-list svg { width: 12px; height: 12px; fill: var(--accent-red); flex: none; }
</style>
</head>
<body>

<section class="card card-front" aria-label="Card front">
  <div class="front-brand"><span class="mark"></span>Valdane Capital</div>
</section>

<section class="card card-back" aria-label="Card back">
  <svg class="back-wave" viewBox="0 0 660 378" preserveAspectRatio="none" aria-hidden="true">
    <path d="M0 268 C120 262 250 300 380 330 C480 352 580 356 660 350 L660 378 L0 378 Z" fill="#ffffff"/>
    <path d="M0 282 C120 278 250 314 380 342 C480 362 580 366 660 360 L660 378 L0 378 Z" fill="#0e0e0e"/>
    <path d="M0 290 C120 288 250 322 380 350 C480 370 580 374 660 368 L660 378 L0 378 Z" fill="#a51c30"/>
  </svg>

  <div class="brand-column">
    <div class="brand-main">Valdane<br>Capital</div>
    <div class="brand-partner"><span class="mark"></span>Thornmere Regional Center</div>
  </div>

  <div class="divider"></div>

  <div class="contact">
    <p class="name">Marcus Valdane</p>
    <p class="title">CEO</p>
    <p class="address">Larkfield Court 5, 4817<br>Vista Orilla, Corvell Bay, CV.</p>
    <ul class="contact-list">
      <li><svg viewBox="0 0 12 12"><path d="M2.5 0.5 L4.5 2.8 L3.4 4.2 C4.2 5.8 5.6 7.3 7.6 8.4 L9 7.4 L11.5 9.3 L10.4 11.4 C5 11 1 7 0.6 1.6 Z"/></svg>+1.555.314.2287</li>
      <li><svg viewBox="0 0 12 12"><rect x="3" y="0.5" width="6" height="11" rx="1.2"/></svg>+1.555.628.4410</li>
      <li><svg viewBox="0 0 12 12"><path d="M0.5 2 H11.5 V10 H0.5 Z M1.5 3 L6 6.5 L10.5 3" stroke="#0e0e0e" stroke-width=".8"/></svg>mvaldane@valdanecompanies.com</li>
      <li><svg viewBox="0 0 12 12"><circle cx="6" cy="6" r="5.5"/><path d="M0.5 6 H11.5 M6 0.5 C3 3.5 3 8.5 6 11.5 M6 0.5 C9 3.5 9 8.5 6 11.5" stroke="#0e0e0e" stroke-width=".7" fill="none"/></svg>www.valdanecompanies.com</li>
    </ul>
  </div>
</section>

</body>
</html>
```